Landing-Page-Design für Immobilienunternehmen
Zielgruppe
Die Firma Kalmt Immobilien kauft jegliche Art von Immobilien im Osten von Hamburg. Die Zielgruppe sind Immobilienbesitzer, welche ihre Wohnung, Haus, Gewerbe oder Sonstiges verkaufen möchten/müssen.
Ich würde gerne drei Unterzielgruppe mehr ansprechen:
Verkauf weil geerbt
textlich untermauert
Verkauf weil ins Altersheim
Verkauf weil ein Geldengpass
Wir kaufen:
Häuser
Eigentumswohnungen
Gewerbeflächen
Mehrfamilienhäuser
Garagen
Agrarflächen (Wald, Acker, Wiese, Teiche)
Aufgabenstellung
Es besteht ein Logo, welches berücksichtigt werden müsste.
Außerdem:
- responsive
- seriös
- conversion optimiert
- viel bebildert, textliche untermauert
- vertrauensvoll/verschwiegen
Telefonnummer soll prominent dargestellt werden, genauso wie ein Kontaktformular.

```html
<!DOCTYPE html>
<html lang="de">
<head>
<meta charset="utf-8">
<title>Kalmt Immobilien – Wir kaufen Immobilien</title>
<link rel="stylesheet" href="https://fonts.googleapis.com/css2?family=Roboto+Condensed:wght@300;400;700&family=Roboto:ital,wght@0,300;0,400;0,700;0,900;1,900&display=swap">
<style>
:root{
  --green:#7ab929;
  --green-dark:#65a01c;
  --ink:#2f3437;
  --text:#555;
  --muted:#8b8b8b;
  --panel:#f4f4f4;
  --bar:#efefef;
  --footer:#231f20;
  --footer-bottom:#111;
  --white:#fff;
}
*{box-sizing:border-box;margin:0;padding:0}
html,body{width:1200px;height:2760px;overflow:hidden}
body{position:relative;background:var(--white);font-family:"Roboto",Arial,sans-serif;color:var(--text)}
.abs{position:absolute}
.band-gray{position:absolute;left:0;top:1064px;width:1200px;height:1518px;background:var(--panel)}

.brand{left:145px;top:96px;width:440px;text-align:center}
.brand-name{display:flex;align-items:center;justify-content:center;gap:14px;font-family:"Roboto Condensed",sans-serif;font-weight:700;font-size:46px;color:var(--ink);letter-spacing:1px;text-transform:uppercase;white-space:nowrap}
.brand-name .dot{width:26px;height:26px;background:var(--green)}
.brand-tag{margin-top:12px;font-family:"Roboto",sans-serif;font-size:15px;letter-spacing:2px;color:var(--ink)}

.promo{left:723px;top:0;width:477px;height:262px}
.promo-text{left:745px;top:48px;width:430px;transform:rotate(-7deg);transform-origin:center center;color:var(--white);text-align:center}
.promo-text .big{font-weight:700;font-size:33px;line-height:38px;white-space:nowrap}
.promo-text .small{margin-top:18px;font-weight:700;font-size:24px;color:var(--ink);white-space:nowrap}

.intro{left:0;top:308px;width:1200px;text-align:center;font-family:"Roboto Condensed",sans-serif}
.intro h1{font-weight:300;font-size:35px;color:var(--green);text-transform:uppercase}
.intro p{margin-top:6px;font-size:25px;color:#444}

.contact-bar{left:70px;top:407px;width:1066px;height:48px;background:var(--bar);display:flex;align-items:center;font-size:21px;letter-spacing:2.4px;color:#444}
.contact-bar .item{position:absolute;display:flex;align-items:center;gap:24px;white-space:nowrap}
.contact-bar svg{width:30px;height:30px}

.card{position:absolute;top:494px;width:339px;height:476px;background:var(--panel)}
.card-head{height:49px;background:var(--green);color:var(--white);font-family:"Roboto Condensed",sans-serif;font-size:23px;display:flex;align-items:center;justify-content:center;text-transform:uppercase;white-space:nowrap}
.card-photo{height:223px}
.card-list{list-style:none;margin:32px 0 0 52px;font-size:16px;line-height:19.8px;color:var(--text)}
.card-list li{display:flex;align-items:center;gap:12px}
.card-list svg{width:13px;height:13px;flex:none}

.call-flag{left:255px;top:956px;width:240px;height:108px}
.call-text{left:330px;top:982px;transform:rotate(-8deg);color:var(--white);font-weight:700;font-size:25px;line-height:26px;text-align:center}
.call-number{left:503px;top:982px;font-weight:900;font-style:italic;font-size:44px;color:var(--green);letter-spacing:1px;white-space:nowrap}

.type{position:absolute;top:1111px;text-align:center}
.type .photo{height:198px}
.type .label{margin-top:14px;font-family:"Roboto Condensed",sans-serif;font-size:20px;color:#333}
.type .more{display:inline-block;margin-top:8px;width:92px;height:27px;background:var(--green);border:2px solid #dcdcdc;color:var(--white);font-family:"Roboto Condensed",sans-serif;font-size:19px;line-height:23px}

.contact-shape{left:0;top:1380px;width:1200px;height:660px}
.contact-head{left:180px;top:1495px;width:480px;transform:rotate(-5deg);text-align:center;color:var(--white);font-weight:700}
.contact-head .t1{font-size:47px}
.contact-head .t2{margin-top:10px;font-size:31px;line-height:34px}
.field{position:absolute;height:44px;background:var(--white);border:1px solid #e0e0e0;font-weight:300;font-size:22px;color:#b5b5b5;padding-left:24px;line-height:42px}
.submit{left:264px;top:1900px;width:216px;height:43px;border-radius:22px;background:#8c8c8c;color:var(--white);font-size:18px;font-weight:500;text-align:center;line-height:43px}

.why{left:0;top:2072px;width:1200px;text-align:center;font-family:"Roboto Condensed",sans-serif}
.why h2{font-weight:300;font-size:35px;color:var(--green);text-transform:uppercase}
.why p{margin-top:8px;font-size:25px;color:#444}
.partner{position:absolute;left:180px;width:800px;display:flex;align-items:flex-start}
.partner-name{width:230px;flex:none;display:flex;align-items:center;gap:10px;font-family:"Roboto Condensed",sans-serif;font-weight:700;font-size:22px;color:#555;padding-top:18px;white-space:nowrap}
.partner-name .sq{width:20px;height:20px;background:#9a9a9a;flex:none}
.partner-text{width:560px;font-size:16px;line-height:20.5px;color:#8a8a8a}

.footer{left:0;top:2582px;width:1200px;height:139px;background:var(--footer);color:#eee;font-size:15px;letter-spacing:2px}
.footer-address{left:72px;top:44px;line-height:18px}
.footer-contact{left:305px;top:36px}
.footer-contact .row{display:flex;align-items:center;gap:16px;height:24px}
.footer-contact svg{width:20px;height:20px}
.footer-brand{right:70px;top:58px;text-align:center}
.footer-brand .name{display:flex;align-items:center;gap:8px;font-family:"Roboto Condensed",sans-serif;font-weight:700;font-size:22px;letter-spacing:1px;color:var(--white);text-transform:uppercase;white-space:nowrap}
.footer-brand .name .dot{width:12px;height:12px;background:var(--green)}
.footer-brand .tag{font-size:9px;letter-spacing:1px;margin-top:4px}
.legal{left:0;top:2721px;width:1200px;height:39px;background:var(--footer-bottom);color:#ddd;font-family:"Roboto Condensed",sans-serif;font-size:10px;letter-spacing:0.8px;padding-left:72px;line-height:34px}
</style>
</head>
<body>
<div class="band-gray"></div>

<!-- Header -->
<div class="abs brand">
  <div class="brand-name"><span class="dot"></span>Kalmt Immobilien</div>
  <div class="brand-tag">VERWALTUNG · BERATUNG · INVESTMENT</div>
</div>

<svg class="abs promo" viewBox="0 0 477 262">
  <defs><filter id="sh" x="-10%" y="-10%" width="130%" height="140%"><feDropShadow dx="0" dy="6" stdDeviation="6" flood-opacity=".25"/></filter></defs>
  <polygon points="0,50 477,0 477,175 405,182 400,203 147,220 148,262 38,218 18,220" fill="#7ab929" filter="url(#sh)"/>
</svg>
<div class="abs promo-text">
  <div class="big">Wir kaufen Immobilien<br>im Osten von Hamburg!</div>
  <div class="small">Diskret, vertraulich &amp; schnell.</div>
</div>

<div class="abs intro">
  <h1>Bei uns ist Ihre Immobilie in guten Händen</h1>
  <p>Egal, warum Sie verkaufen wollen!</p>
</div>

<div class="abs contact-bar">
  <div class="item" style="left:22px">
    <svg viewBox="0 0 24 24"><path fill="#7ab929" d="M6.6 10.8a15 15 0 0 0 6.6 6.6l2.2-2.2c.3-.3.7-.4 1-.2 1.1.4 2.3.6 3.6.6.6 0 1 .4 1 1V20c0 .6-.4 1-1 1A17 17 0 0 1 3 4c0-.6.4-1 1-1h3.5c.6 0 1 .4 1 1 0 1.3.2 2.5.6 3.6.1.3 0 .7-.2 1z"/></svg>
    <span>04107 / 532 40 -20</span>
  </div>
  <div class="item" style="left:378px">
    <svg viewBox="0 0 24 24"><rect x="2" y="5" width="20" height="14" fill="none" stroke="#7ab929" stroke-width="2"/><path d="M2 5l10 8 10-8" fill="none" stroke="#7ab929" stroke-width="2"/></svg>
    <span>kontakt@kalmt-immobilien.de</span>
  </div>
  <div class="item" style="left:840px">
    <svg viewBox="0 0 24 24"><rect x="6" y="2" width="12" height="20" rx="2" fill="#7ab929"/><rect x="8" y="5" width="8" height="12" fill="#fff"/></svg>
    <span>0176/4829015</span>
  </div>
</div>

<!-- Reasons -->
<div class="card" style="left:68px">
  <div class="card-head">Sie haben geerbt?</div>
  <div class="card-photo" role="img" aria-label="Foto: ältere Hände halten ein kleines Holzhaus" style="background:linear-gradient(160deg,#d8dadb,#b9b3ad 55%,#c9cbcc)"></div>
  <ul class="card-list">
    <li><svg viewBox="0 0 12 12"><path d="M2 1l5 5-5 5" fill="none" stroke="#7ab929" stroke-width="2.4"/></svg>At vero eos et accusam</li>
    <li><svg viewBox="0 0 12 12"><path d="M2 1l5 5-5 5" fill="none" stroke="#333" stroke-width="2.4"/></svg>duo dolores et ea rebum.</li>
    <li><svg viewBox="0 0 12 12"><path d="M2 1l5 5-5 5" fill="none" stroke="#7ab929" stroke-width="2.4"/></svg>Stet clita kasd gubergren</li>
    <li><svg viewBox="0 0 12 12"><path d="M2 1l5 5-5 5" fill="none" stroke="#333" stroke-width="2.4"/></svg>sea takimata sanctus est</li>
    <li><svg viewBox="0 0 12 12"><path d="M2 1l5 5-5 5" fill="none" stroke="#7ab929" stroke-width="2.4"/></svg>Lorem ipsum dolor sit amet.</li>
    <li><svg viewBox="0 0 12 12"><path d="M2 1l5 5-5 5" fill="none" stroke="#333" stroke-width="2.4"/></svg>dolor sit amet, consetetur</li>
  </ul>
</div>
<div class="card" style="left:431px">
  <div class="card-head">Verkauf aus Altersgründen?</div>
  <div class="card-photo" role="img" aria-label="Foto: Nahaufnahme eines älteren Menschen" style="background:linear-gradient(100deg,#f3f1ef,#d9c9bd 55%,#b99c8a)"></div>
  <ul class="card-list">
    <li><svg viewBox="0 0 12 12"><path d="M2 1l5 5-5 5" fill="none" stroke="#7ab929" stroke-width="2.4"/></svg>At vero eos et accusam</li>
    <li><svg viewBox="0 0 12 12"><path d="M2 1l5 5-5 5" fill="none" stroke="#333" stroke-width="2.4"/></svg>duo dolores et ea rebum.</li>
    <li><svg viewBox="0 0 12 12"><path d="M2 1l5 5-5 5" fill="none" stroke="#7ab929" stroke-width="2.4"/></svg>Stet clita kasd gubergren</li>
    <li><svg viewBox="0 0 12 12"><path d="M2 1l5 5-5 5" fill="none" stroke="#333" stroke-width="2.4"/></svg>sea takimata sanctus est</li>
    <li><svg viewBox="0 0 12 12"><path d="M2 1l5 5-5 5" fill="none" stroke="#7ab929" stroke-width="2.4"/></svg>Lorem ipsum dolor sit amet.</li>
    <li><svg viewBox="0 0 12 12"><path d="M2 1l5 5-5 5" fill="none" stroke="#333" stroke-width="2.4"/></svg>dolor sit amet, consetetur</li>
  </ul>
</div>
<div class="card" style="left:800px">
  <div class="card-head">Diskret &amp; schnell!</div>
  <div class="card-photo" role="img" aria-label="Foto: Mann zeigt leere Hosentasche" style="background:linear-gradient(90deg,#2e2b27,#6d675e 50%,#e9e9e9 85%)"></div>
  <ul class="card-list">
    <li><svg viewBox="0 0 12 12"><path d="M2 1l5 5-5 5" fill="none" stroke="#7ab929" stroke-width="2.4"/></svg>At vero eos et accusam</li>
    <li><svg viewBox="0 0 12 12"><path d="M2 1l5 5-5 5" fill="none" stroke="#333" stroke-width="2.4"/></svg>duo dolores et ea rebum.</li>
    <li><svg viewBox="0 0 12 12"><path d="M2 1l5 5-5 5" fill="none" stroke="#7ab929" stroke-width="2.4"/></svg>Stet clita kasd gubergren</li>
    <li><svg viewBox="0 0 12 12"><path d="M2 1l5 5-5 5" fill="none" stroke="#333" stroke-width="2.4"/></svg>sea takimata sanctus est</li>
    <li><svg viewBox="0 0 12 12"><path d="M2 1l5 5-5 5" fill="none" stroke="#7ab929" stroke-width="2.4"/></svg>Lorem ipsum dolor sit amet.</li>
    <li><svg viewBox="0 0 12 12"><path d="M2 1l5 5-5 5" fill="none" stroke="#333" stroke-width="2.4"/></svg>dolor sit amet, consetetur</li>
  </ul>
</div>

<!-- Call to action -->
<svg class="abs call-flag" viewBox="0 0 240 108">
  <defs><filter id="sh2" x="-10%" y="-10%" width="130%" height="140%"><feDropShadow dx="0" dy="5" stdDeviation="5" flood-opacity=".25"/></filter></defs>
  <polygon points="0,26 236,0 229,82 20,100 12,108 8,92" fill="#7ab929" filter="url(#sh2)"/>
  <g transform="translate(22,50) rotate(-8)">
    <path fill="#fff" d="M8 4c-3 2-4 6-2 11 3 8 10 15 18 18 5 2 9 1 11-2l-6-6-5 3c-4-2-8-6-10-10l3-5z"/>
    <path d="M26 5a12 12 0 0 1 10 10M24 11a6 6 0 0 1 6 6" fill="none" stroke="#fff" stroke-width="2.5"/>
  </g>
</svg>
<div class="abs call-text">Rufen Sie<br>mich an!</div>
<div class="abs call-number">04107 532 40 - 20</div>

<!-- Property types -->
<div class="type" style="left:74px;width:201px">
  <div class="photo" role="img" aria-label="Foto: weißes Einfamilienhaus mit rotem Dach" style="background:linear-gradient(180deg,#9cc0e0,#eef0ee 45%,#b6624b 60%,#6a7f4b)"></div>
  <div class="label">Häuser</div><span class="more">MEHR</span>
</div>
<div class="type" style="left:291px;width:201px">
  <div class="photo" role="img" aria-label="Foto: helle leere Wohnung mit Küche" style="background:linear-gradient(90deg,#f6f6f6,#e2e2e2 60%,#6d6a5f 80%,#d9d9d9)"></div>
  <div class="label">Eigentumswohnungen</div><span class="more">MEHR</span>
</div>
<div class="type" style="left:511px;width:197px">
  <div class="photo" role="img" aria-label="Luftbild: Gewerbegebiet mit Hallen" style="background:linear-gradient(150deg,#5f7e3c,#b9bfc2 45%,#7b9a4f)"></div>
  <div class="label">Gewerbeflächen</div><span class="more">MEHR</span>
</div>
<div class="type" style="left:727px;width:202px">
  <div class="photo" role="img" aria-label="Foto: weißes Altbau-Mehrfamilienhaus" style="background:linear-gradient(180deg,#8fb4d8,#f0ede6 40%,#d9d4c8)"></div>
  <div class="label">Mehrfamilienhäuser</div><span class="more">MEHR</span>
</div>
<div class="type" style="left:941px;width:198px">
  <div class="photo" role="img" aria-label="Foto: blaue Garage mit weißen Toren" style="background:linear-gradient(180deg,#a8c2e0,#3f5f8f 40%,#ececec 75%,#8a8a80)"></div>
  <div class="label">Garagen</div><span class="more">MEHR</span>
</div>

<!-- Contact form -->
<svg class="abs contact-shape" viewBox="0 1380 1200 660">
  <defs><filter id="sh3" x="-5%" y="-5%" width="110%" height="115%"><feDropShadow dx="0" dy="8" stdDeviation="8" flood-opacity=".25"/></filter></defs>
  <path d="M0 1511 L830 1423 L680 1920 Q660 1960 600 1962 L0 2020 Z" fill="#7ab929" filter="url(#sh3)"/>
</svg>
<svg class="abs" style="left:766px;top:1387px;width:434px;height:542px" viewBox="0 0 434 542" role="img" aria-label="Foto: weißes Haus mit Garten">
  <defs><linearGradient id="house" x1="0" y1="0" x2="0" y2="1"><stop offset="0" stop-color="#8fb6dc"/><stop offset=".35" stop-color="#eef0f0"/><stop offset=".55" stop-color="#c0715a"/><stop offset=".7" stop-color="#e6e6e2"/><stop offset="1" stop-color="#6f8a4c"/></linearGradient></defs>
  <polygon points="64,36 434,0 434,499 0,542" fill="url(#house)"/>
</svg>
<div class="abs contact-head">
  <div class="t1">Kontakt starten:</div>
  <div class="t2">Nehmen Sie unverbindlich<br>und vertrauensvoll<br>Kontakt mit mir auf!</div>
</div>
<div class="field" style="left:147px;top:1711px;width:486px">Vollständiger Name</div>
<div class="field" style="left:147px;top:1766px;width:486px">Art der Immobilie</div>
<div class="field" style="left:147px;top:1820px;width:208px">e-mail</div>
<div class="field" style="left:423px;top:1820px;width:210px">Telefon</div>
<div class="abs submit">Kontakt starten</div>

<!-- Partners -->
<div class="abs why">
  <h2>Warum sollten auch Sie mit mir zusammmearbeiten?</h2>
  <p>Unsere langjährigen Geschäftspartner:</p>
</div>
<div class="partner" style="top:2181px">
  <div class="partner-name"><span class="sq"></span>Elbkasse</div>
  <p class="partner-text">At vero eos et accusam et justo duo dolores et ea rebum. Stet clita kasd guberg-ren, no sea takimata sanctus est Lorem ipsum dolor sit amet. Lorem ipsum dolor sit amet, consetetur sadipscing elitr, sed diam nonu</p>
</div>
<div class="partner" style="top:2279px">
  <div class="partner-name"><span class="sq"></span>Hansa Fonds</div>
  <p class="partner-text">At vero eos et accusam et justo duo dolores et ea rebum. Stet clita kasd guberg-ren, no sea takimata sanctus est Lorem ipsum dolor sit amet. Lorem ipsum dolor sit amet, consetetur sadipscing elitr, sed diam nonu</p>
</div>
<div class="partner" style="top:2378px">
  <div class="partner-name"><span class="sq"></span>Brenner Immobilien</div>
  <p class="partner-text">At vero eos et accusam et justo duo dolores et ea rebum. Stet clita kasd guberg-ren, no sea takimata sanctus est Lorem ipsum dolor sit amet. Lorem ipsum dolor sit amet, consetetur sadipscing elitr, sed diam nonu</p>
</div>
<div class="partner" style="top:2476px">
  <div class="partner-name"><span class="sq"></span>Notariat Hafenkante</div>
  <p class="partner-text">At vero eos et accusam et justo duo dolores et ea rebum. Stet clita kasd guberg-ren, no sea takimata sanctus est Lorem ipsum dolor sit amet. Lorem ipsum dolor sit amet, consetetur sadipscing elitr, sed diam nonu</p>
</div>

<!-- Footer -->
<div class="abs footer">
  <div class="abs footer-address">Kalmt Immobilien<br>Lindenstieg 12<br>21509 Glindhorst</div>
  <div class="abs footer-contact">
    <div class="row"><svg viewBox="0 0 24 24"><path fill="#7ab929" d="M6.6 10.8a15 15 0 0 0 6.6 6.6l2.2-2.2c.3-.3.7-.4 1-.2 1.1.4 2.3.6 3.6.6.6 0 1 .4 1 1V20c0 .6-.4 1-1 1A17 17 0 0 1 3 4c0-.6.4-1 1-1h3.5c.6 0 1 .4 1 1 0 1.3.2 2.5.6 3.6.1.3 0 .7-.2 1z"/></svg>04107 / 532 40 -20</div>
    <div class="row"><svg viewBox="0 0 24 24"><rect x="2" y="5" width="20" height="14" fill="#7ab929"/><path d="M2 5l10 8 10-8" fill="none" stroke="#231f20" stroke-width="2"/></svg>kontakt@kalmt-immobilien.de</div>
    <div class="row"><svg viewBox="0 0 24 24"><rect x="6" y="2" width="12" height="20" rx="2" fill="#7ab929"/><rect x="8" y="5" width="8" height="12" fill="#231f20"/></svg>0176/4829015</div>
  </div>
  <div class="abs footer-brand">
    <div class="name"><span class="dot"></span>Kalmt Immobilien</div>
    <div class="tag">VERWALTUNG · BERATUNG · INVESTMENT</div>
  </div>
</div>
<div class="abs legal">KONTAKT &nbsp;|&nbsp; AGB &nbsp;|&nbsp; WIDERRUFSRECHT &nbsp;|&nbsp; ZAHLUNGSINFORMATION &nbsp;|&nbsp; DATENSCHUTZ &nbsp;|&nbsp; IMPRESSUM</div>
</body>
</html>
```